Product Page Images & A+ Content Design for TCG Storage Products

Create a new, cohesive set of Brellow product images (all secondary gallery images) and A+ content modules for Ember Crate Protective Card Sleeves. The goal is to clearly communicate protection, fit, clarity, and archival safety while looking more premium and distinctive than competing sleeve brands.

Primary benefits to communicate:
- Shield your cards from wear – blocks dust and resists surface scratches.
- The perfect fit for your collection – designed to fit all standard trading cards.
- Ultra‑clear smooth finish.
- Archival‑safe high‑quality materials – acid‑free, no PVC, non‑toxic, long‑term storage.

Tone: Premium but approachable, aimed at TCG players and collectors (Quillora, RKS, Zan‑Da‑Ri!, sports cards, etc.). Colour/theme be in keeping with the packaging design. Dark, with a pop of orange. Perhaps subtle textures or patterns, with a mythic/fantasy feel.

Existing product content is attached for reference.

Target Market(s)

Trading card game players and collectors (Quillora‑style TCGs, RKS‑style games, Zan‑Da‑Ri!‑style games, sports cards). Age: Mainly 14–40, skewed to hobbyist young adults. They care about condition and long‑term value of their cards, enjoy customising and protecting decks, responsive to “premium but good value” messaging.

Industry/Entity Type

Trading card accessories / tabletop gaming accessories. Protective sleeves and storage for trading card games and sports cards.

Font styles to use
Sans Serif

Requirements
Must have
• Clear communication of the four key benefits listed in the Project Description. Consistent use of Ember Crate logo and brand colours. Text that is readable on mobile thumbnails. Clean, uncluttered layouts that look professional next to leading competitors.
Nice to have
• Subtle fantasy / “mythic” visual touches that support the brand name (background textures, icons, gentle glow effects). Simple line‑art icons for key benefits (dust, scratch, fit, clarity, archival safe). Visual references to different card types (TCG, sports, etc.) using generic, non‑IP artwork. Light environmental storytelling (desk, playmat, storage box, binder). Lifestyle shots showing people playing or organising their collections.
Should not have
• Any copyrighted or licensed character artwork or logos. Over‑busy backgrounds or textures that distract from the product. Very long text blocks or small copy that is hard to read on mobile. Edgy, aggressive, or dark imagery that clashes with a family‑friendly hobby product. Inconsistent typography or colour schemes across images.

```html
<!DOCTYPE html>
<html lang="en">
<head>
<meta charset="utf-8">
<title>Ember Crate Protective Card Sleeves – Gallery Set</title>
<link rel="stylesheet" href="https://fonts.googleapis.com/css2?family=Poppins:wght@400;500;600;700;800&family=Cinzel:wght@700;900&display=swap">
<style>
:root{
  --board:#5a5a5a;
  --ink:#0b0b0b;
  --night:#141414;
  --ember:#f0501e;
  --ember-deep:#c8360e;
  --gold:#f7c51e;
  --white:#ffffff;
  --paper:#f2f2f2;
  --navy:#1f2a35;
}
*{box-sizing:border-box;margin:0;padding:0}
html,body{width:1200px;height:791px;overflow:hidden}
body{background:var(--board);font-family:"Poppins",sans-serif;position:relative}

.panel{position:absolute;width:303px;height:172px;overflow:hidden;box-shadow:0 6px 14px rgba(0,0,0,.45)}
.col-1{left:97px}.col-2{left:448px}.col-3{left:803px}
.row-1{top:190px}.row-2{top:408px}

.speckle{background:
  radial-gradient(circle at 12% 30%,rgba(200,40,20,.55) 0 1px,transparent 2px),
  radial-gradient(circle at 78% 18%,rgba(200,40,20,.5) 0 1px,transparent 2px),
  radial-gradient(circle at 35% 70%,rgba(200,40,20,.45) 0 1px,transparent 2px),
  radial-gradient(circle at 88% 62%,rgba(200,40,20,.5) 0 1px,transparent 2px),
  radial-gradient(circle at 55% 12%,rgba(200,40,20,.4) 0 1px,transparent 2px),
  var(--ink)}

.brand{position:absolute;display:flex;align-items:center;gap:4px;color:var(--white);font-weight:700;font-size:7px;letter-spacing:.5px;line-height:1}
.brand-dot{width:10px;height:10px;border-radius:50%;background:var(--ember)}
.brand.center{left:50%;transform:translateX(-50%);top:10px}
.brand.left{left:12px;top:14px}

/* Sleeve box: sized by font-size (1em ≈ width/10) */
.pack{position:absolute;display:flex;flex-direction:column;border:.25em solid var(--white);border-radius:.2em;
  background:var(--ember);box-shadow:0 3px 8px rgba(0,0,0,.5);overflow:hidden}
.pack-top{display:flex;justify-content:space-between;align-items:center;background:var(--night);padding:.5em .6em;height:22%}
.pack-dot{width:1.6em;height:1.6em;border-radius:50%;background:var(--ember)}
.pack-count{background:var(--ember);color:var(--white);font-family:"Cinzel",serif;font-weight:900;font-size:1.6em;line-height:1;padding:.1em .25em}
.pack-title{font-family:"Cinzel",serif;font-weight:900;color:var(--gold);font-size:1.25em;line-height:1.05;text-align:center;padding:.35em .2em;text-shadow:0 1px 0 var(--ink)}
.pack-art{flex:1;margin:0 .5em .5em;background:radial-gradient(ellipse at 60% 50%,#4a6a86,var(--navy) 70%);border-radius:.2em}

.art{position:absolute}
.dragon{background:radial-gradient(ellipse at 50% 70%,#e2561c 0,#7a2a10 45%,transparent 75%)}

.plate{position:absolute;left:50%;transform:translateX(-50%);bottom:12px;width:150px;padding:3px 0;
  background:linear-gradient(180deg,#3a3a3a,#1c1c1c);border:1px solid #6b6b6b;text-align:center;
  font-family:"Cinzel",serif;font-weight:700;line-height:1.15}
.plate .l1{color:var(--paper);font-size:7px}
.plate .l2{color:var(--ember);font-size:7px}

.headline{position:absolute;font-weight:700;font-size:13px;line-height:1.15}
.headline.orange{color:var(--ember)}
.headline.white{color:var(--white)}
.sub{position:absolute;font-size:7px;font-weight:500;line-height:1.25}
.sub.dark-text{color:var(--ink)}
.sub.orange{color:var(--ember);font-weight:600}

.benefits{position:absolute;list-style:none;display:flex;flex-direction:column;gap:6px}
.benefits.inline{flex-direction:row;gap:12px}
.benefit{display:flex;align-items:flex-start;gap:5px;font-size:7px;font-weight:600;color:var(--ink);line-height:1.2}
.benefit-icon{flex:none;width:11px;height:11px;border-radius:50%;background:radial-gradient(circle,var(--gold) 0 25%,var(--ember) 30%)}

.cut{position:absolute;inset:0}

.size-tag{position:absolute;background:var(--gold);color:var(--ink);font-size:6.5px;font-weight:700;padding:3px 6px}
.size-values{position:absolute;display:flex;gap:20px;color:var(--white);font-size:7px;font-weight:500}
.dim{position:absolute;color:var(--white);font-size:7px;font-weight:600}
.dim.vertical{transform:rotate(-90deg);transform-origin:left top}

.floor{position:absolute;left:0;right:0;bottom:0;background:linear-gradient(180deg,#e8e8e8,var(--white))}
</style>
</head>
<body>

<!-- Hero -->
<section class="panel row-1 col-1 speckle">
  <div class="brand center"><span class="brand-dot"></span>EMBER CRATE</div>
  <div class="art dragon" role="img" aria-label="Fiery dragon illustration, left" style="left:0;top:70px;width:90px;height:100px"></div>
  <div class="art dragon" role="img" aria-label="Fiery dragon illustration, right" style="right:0;top:70px;width:90px;height:100px"></div>
  <div class="pack" style="left:76px;top:42px;width:52px;height:72px;font-size:5.2px"><div class="pack-top"><span class="pack-dot"></span><span class="pack-count">100</span></div><div class="pack-title">PROTECTIVE CARD SLEEVES</div><div class="pack-art" role="img" aria-label="Card artwork"></div></div>
  <div class="pack" style="left:176px;top:42px;width:52px;height:72px;font-size:5.2px"><div class="pack-top"><span class="pack-dot"></span><span class="pack-count">100</span></div><div class="pack-title">PROTECTIVE CARD SLEEVES</div><div class="pack-art" role="img" aria-label="Card artwork"></div></div>
  <div class="pack" style="left:120px;top:34px;width:62px;height:86px;font-size:6.2px"><div class="pack-top"><span class="pack-dot"></span><span class="pack-count">100</span></div><div class="pack-title">PROTECTIVE CARD SLEEVES</div><div class="pack-art" role="img" aria-label="Card artwork"></div></div>
  <div class="plate"><div class="l1">PROTECTIVE CARD SLEEVES</div><div class="l2">100 SLEEVES</div></div>
</section>

<!-- Protection -->
<section class="panel row-1 col-2" style="background:var(--white)">
  <svg class="cut" viewBox="0 0 303 172" aria-hidden="true"><polygon points="0,0 303,0 303,22 150,22 110,48 0,48" fill="#0b0b0b"/></svg>
  <div class="brand left"><span class="brand-dot"></span>EMBER CRATE</div>
  <h2 class="headline orange" style="left:12px;top:54px;width:130px">Shield your cards from wear</h2>
  <p class="sub dark-text" style="left:12px;top:86px;width:105px">Blocks dust and resists surface scratches</p>
  <ul class="benefits" style="left:12px;top:108px">
    <li class="benefit"><span class="benefit-icon"></span>Dust protection</li>
    <li class="benefit"><span class="benefit-icon"></span>Scratch resistant</li>
  </ul>
  <div class="pack" style="left:180px;top:24px;width:80px;height:112px;font-size:8px"><div class="pack-top"><span class="pack-dot"></span><span class="pack-count">100</span></div><div class="pack-title">PROTECTIVE CARD SLEEVES</div><div class="pack-art" role="img" aria-label="Card artwork"></div></div>
  <svg style="position:absolute;left:118px;top:92px" width="56" height="58" viewBox="0 0 56 58" role="img" aria-label="Protect dust and scratch badge">
    <path d="M28 2 L52 10 V28 C52 42 40 52 28 56 C16 52 4 42 4 28 V10 Z" fill="#f7c51e" stroke="#0b0b0b" stroke-width="1.5"/>
    <text x="28" y="26" text-anchor="middle" font-family="Poppins,sans-serif" font-size="8" font-weight="700" fill="#0b0b0b">Protect</text>
    <text x="28" y="35" text-anchor="middle" font-family="Poppins,sans-serif" font-size="4.5" font-weight="600" fill="#0b0b0b">DUST &amp;</text>
    <text x="28" y="41" text-anchor="middle" font-family="Poppins,sans-serif" font-size="4.5" font-weight="600" fill="#0b0b0b">SCRATCH</text>
  </svg>
</section>

<!-- Fit -->
<section class="panel row-1 col-3" style="background:linear-gradient(90deg,#050505,#1e1e1e)">
  <div class="brand left"><span class="brand-dot"></span>EMBER CRATE</div>
  <h2 class="headline white" style="left:12px;top:46px;width:125px">The perfect fit for your collection</h2>
  <p class="sub orange" style="left:12px;top:80px;width:120px">Designed to fit all standard trading cards</p>
  <div class="size-tag" style="left:12px;top:104px">Trading Card Size</div>
  <div class="size-values" style="left:12px;top:126px"><span>63 x 88mm</span><span>2.5" x 3.5"</span></div>
  <span class="dim" style="left:208px;top:18px">63mm</span>
  <span class="dim vertical" style="left:178px;top:100px">88mm</span>
  <div class="pack" style="left:190px;top:30px;width:68px;height:96px;font-size:6.8px"><div class="pack-top"><span class="pack-dot"></span><span class="pack-count">100</span></div><div class="pack-title">PROTECTIVE CARD SLEEVES</div><div class="pack-art" role="img" aria-label="Card artwork"></div></div>
</section>

<!-- Clarity -->
<section class="panel row-2 col-1" style="background:var(--white)">
  <svg class="cut" viewBox="0 0 303 172" aria-hidden="true"><polygon points="0,0 303,0 303,22 150,22 110,40 0,40" fill="#0b0b0b"/></svg>
  <div class="brand left"><span class="brand-dot"></span>EMBER CRATE</div>
  <h2 class="headline orange" style="left:12px;top:52px;width:100px">Ultra-clear smooth finish</h2>
  <ul class="benefits" style="left:12px;top:88px;width:118px;gap:8px">
    <li class="benefit"><span class="benefit-icon"></span>Enjoy crystal-clear visibility for vibrant artwork and sharp details</li>
    <li class="benefit"><span class="benefit-icon"></span>Silky smooth feel that makes shuffling easy</li>
  </ul>
  <div class="pack" style="left:168px;top:22px;width:64px;height:88px;transform:rotate(-6deg);font-size:6.4px"><div class="pack-top"><span class="pack-dot"></span><span class="pack-count">100</span></div><div class="pack-title">PROTECTIVE CARD SLEEVES</div><div class="pack-art" role="img" aria-label="Card artwork"></div></div>
  <div class="pack" style="left:186px;top:36px;width:72px;height:100px;font-size:7.2px"><div class="pack-top"><span class="pack-dot"></span><span class="pack-count">100</span></div><div class="pack-title">PROTECTIVE CARD SLEEVES</div><div class="pack-art" role="img" aria-label="Card artwork"></div></div>
</section>

<!-- Archival -->
<section class="panel row-2 col-2" style="background:linear-gradient(180deg,var(--ink) 0 61%,var(--white) 61%)">
  <div class="brand left"><span class="brand-dot"></span>EMBER CRATE</div>
  <h2 class="headline white" style="left:12px;top:46px;width:105px">Archival-safe high quality materials</h2>
  <p class="sub orange" style="left:12px;top:110px;width:110px">Preserve your collection for years without damage or yellowing</p>
  <ul class="benefits inline" style="left:12px;top:148px">
    <li class="benefit"><span class="benefit-icon"></span>Acid-free</li>
    <li class="benefit"><span class="benefit-icon"></span>Non-toxic</li>
  </ul>
  <div class="pack" style="left:205px;top:26px;width:66px;height:92px;transform:rotate(8deg);font-size:6.6px"><div class="pack-top"><span class="pack-dot"></span><span class="pack-count">100</span></div><div class="pack-title">PROTECTIVE CARD SLEEVES</div><div class="pack-art" role="img" aria-label="Card artwork"></div></div>
  <div class="pack" style="left:140px;top:30px;width:72px;height:104px;transform:rotate(-8deg);font-size:7.2px"><div class="pack-top"><span class="pack-dot"></span><span class="pack-count">100</span></div><div class="pack-title">PROTECTIVE CARD SLEEVES</div><div class="pack-art" role="img" aria-label="Card artwork"></div></div>
</section>

<!-- Lineup -->
<section class="panel row-2 col-3 speckle">
  <div class="floor" style="height:52px"></div>
  <div class="brand center"><span class="brand-dot"></span>EMBER CRATE</div>
  <div class="pack" style="left:52px;top:46px;width:62px;height:88px;font-size:6.2px"><div class="pack-top"><span class="pack-dot"></span><span class="pack-count">100</span></div><div class="pack-title">PROTECTIVE CARD SLEEVES</div><div class="pack-art" role="img" aria-label="Card artwork"></div></div>
  <div class="pack" style="left:189px;top:46px;width:62px;height:88px;font-size:6.2px"><div class="pack-top"><span class="pack-dot"></span><span class="pack-count">100</span></div><div class="pack-title">PROTECTIVE CARD SLEEVES</div><div class="pack-art" role="img" aria-label="Card artwork"></div></div>
  <div class="pack" style="left:110px;top:38px;width:80px;height:104px;font-size:8px"><div class="pack-top"><span class="pack-dot"></span><span class="pack-count">100</span></div><div class="pack-title">PROTECTIVE CARD SLEEVES</div><div class="pack-art" role="img" aria-label="Card artwork"></div></div>
</section>

</body>
</html>
```